Employment Agency Website Design

We are working with an employment agency in California.

Some sites to use for content/competitors and inspiration:

https://www.pinecrestjobs.com/us/en
https://www.velmorusa.com
https://www.dravenworks.us
https://www.quillora.com/en
https://www.tomvalusa.com
https://www.fernstaffing.com

Thank you for taking the time to consider designing a website for us. We are web developers based in Stockton, CA, USA. Most of our projects go through the same process. Understanding this process may help you win a project with us. We custom-code all of our websites in-house. We don’t have any requirements as to what tools you use for your design, but we prefer Figma files. For any design that we label as four-stars, we send it to the client for review. The client picks the final design they want us to use. Once we complete this process, we will continue to show additional clients all the four-star sites and purchase them later. Your designs will have multiple chances to sell. For better chances of success, we ask that you follow these guidelines.

IMAGES:
If you use any images or icons in the design, we ask that you have a link to the asset so we can purchase the image/icon. Most of the designs we submit do not have the customer’s images on them unless they have some great images. Be creative; show us the feeling you are trying to portray with your image choices. Use any royalty-free site you choose. We subscribe to Adobe and mainly use their images, but we can purchase images outside of Adobe. PLEASE NOTE: we will not submit designs to clients with watermarks on the images.

FONTS:
We ask that you identify the fonts used in the design. This can be done in a message if you want. We typically use Google Fonts and Adobe Fonts.

CONTENT:
We're always open to different content and ideas. We often submit designs with stock images so the client can see our vision. We typically take pictures after the website launch to use their images with our vision. Lorem Ipsum is fine for paragraphs, but we ask that you write the headers in correct English. We want to be able to show the vision and identify the sections of the website.

INSPIRATION:
We typically add a couple of links in the brief of websites we like to help you get started in your design.

REVISIONS:
We do not often ask for revisions of the designs unless we see something in the design that may not appeal to the client. If there are slight changes that we want to make, we do that in the development process.

FEEDBACK:
We rarely give feedback on designs during the design process. We are working on many website projects and do not have the time to provide feedback. We usually respond if your request is well thought out and asks specific questions, but a note asking “feedback, please” usually goes unanswered.

```html
<!DOCTYPE html>
<html lang="en">
<head>
<meta charset="utf-8">
<title>Kestrel Talent — The Future Of Work</title>
<link href="https://fonts.googleapis.com/css2?family=Montserrat:wght@400;500;600;700;800&family=Open+Sans:wght@400;600&display=swap" rel="stylesheet">
<style>
:root{
  --red:#c51f30;
  --ink:#222428;
  --text:#555a60;
  --white:#ffffff;
  --field:#f3f3f4;
  --footer:#0c0c0d;
  --head:'Montserrat',sans-serif;
  --body:'Open Sans',sans-serif;
}
*{box-sizing:border-box;margin:0;padding:0}
html,body{width:1200px;height:4227px;overflow:hidden}
body{position:relative;font-family:var(--body);color:var(--text);background:var(--white)}
.abs{position:absolute}
.btn{position:absolute;display:inline-flex;align-items:center;gap:6px;font-family:var(--head);font-weight:700;font-size:13px;color:var(--white);background:var(--red);border-radius:24px;padding:0 20px;height:44px;letter-spacing:.2px;text-decoration:none}
.btn .dot{width:12px;height:12px;border-radius:50%;background:var(--white);display:inline-block;position:relative}
.btn .dot::after{content:"";position:absolute;left:4px;top:3px;border-left:5px solid var(--red);border-top:3px solid transparent;border-bottom:3px solid transparent}
.btn.outline{background:transparent;border:2px solid var(--white)}
.h2{font-family:var(--head);font-weight:700;font-size:34px;color:var(--ink);letter-spacing:.3px}
.h2 em{font-style:normal;color:var(--red)}
.para{font-size:14.5px;line-height:25.6px;color:var(--text)}
.brand-name{font-family:var(--head);font-weight:600;color:var(--white);display:flex;align-items:center;gap:10px}
.brand-name .sq{width:24px;height:24px;background:var(--white);border-radius:3px;flex:none}
.brand-line{font-size:11px;color:#d6d6d6;margin-left:34px;margin-top:2px}

/* hero */
.hero{left:0;top:0;width:1200px;height:600px;background:linear-gradient(180deg,#1b1d22 0%,#25262a 55%,#2e2a27 100%)}
.hero-photo{left:700px;top:135px;width:330px;height:380px;border-radius:30px;background:radial-gradient(ellipse at 55% 55%,#e0743a 0%,#8a4a33 30%,#3a3436 62%,rgba(40,40,44,0) 85%)}
.nav-line{left:112px;top:89px;width:976px;height:1px;background:rgba(255,255,255,.18)}
.brand{left:112px;top:22px}
.brand .brand-name{font-size:28px}
.nav a{position:absolute;top:36px;color:var(--white);font-size:15px;text-decoration:none}
.login{left:980px;top:24px;height:46px}
.welcome{left:112px;top:212px;font-family:var(--head);font-size:27px;color:var(--white)}
.hero-title{left:110px;top:252px;font-family:var(--head);font-weight:800;font-size:60px;color:var(--white);line-height:72px}
.hero-sub{left:112px;top:333px;font-family:var(--head);font-size:32px;color:var(--white)}
.slides{left:537px;top:544px;display:flex;gap:8px}
.slides span{width:36px;height:6px;border-radius:3px;background:var(--white)}
.slides span:first-child{background:var(--red)}

/* about */
.about-frame{left:163px;top:718px;width:433px;height:467px;border-right:2px solid var(--red);border-bottom:2px solid var(--red)}
.about-photo{left:153px;top:703px;width:430px;height:470px;background:linear-gradient(135deg,#a35a4a 0%,#7f8a93 40%,#5b86b0 65%,#cfd3d6 100%)}
.about-block{left:84px;top:1060px;width:136px;height:150px;background:var(--red);border-radius:10px}
.dots{display:grid}
.dots i{width:4px;height:4px;border-radius:50%;background:var(--red);display:block}
.about h2{position:absolute;left:653px;top:744px}
.about .para{position:absolute;left:653px;top:820px;width:435px}
.about .btn{left:653px;top:1113px}

/* services */
.services h2{position:absolute;left:108px;top:1302px;line-height:52px}
.services .para{position:absolute;left:653px;top:1306px;width:435px}
.services-band{left:0;top:1727px;width:1200px;height:328px;background:linear-gradient(90deg,#d9d9dc,#eeeeef 40%,#e4e4e6 70%,#d3d3d6)}
.grid{left:184px;top:1466px;width:832px;display:grid;grid-template-columns:repeat(4,208px);grid-template-rows:259px 259px;box-shadow:0 6px 20px rgba(0,0,0,.08)}
.cell{background:var(--white);padding:28px 18px 0 21px}
.cell svg{display:block}
.cell h3{font-family:var(--head);font-weight:600;font-size:17px;line-height:25px;color:var(--ink);margin-top:12px}
.cell p{font-size:12px;line-height:18.5px;color:var(--text);margin-top:8px}
.cell a{display:inline-block;margin-top:10px;font-size:12px;color:var(--red);font-weight:600;border-bottom:1px solid var(--red)}
.ph-ware{background:linear-gradient(160deg,#c8a37a,#8c6b4b 60%,#b7b2a8)}
.ph-acct{background:linear-gradient(150deg,#e7c8a4,#d0a986 50%,#f0ebe5)}
.ph-office{background:linear-gradient(150deg,#2d2f33,#56585d 50%,#1d1e21)}
.ph-mfg{background:linear-gradient(150deg,#6e7780,#3c4750 50%,#9aa3aa)}

/* join */
.join{left:0;top:2055px;width:1200px;height:427px;background:linear-gradient(90deg,#c62838,#cf3a48 55%,#c12434)}
.join-title{left:112px;top:2120px;font-family:var(--head);font-weight:700;font-size:34px;line-height:52px;color:var(--white)}
.join-text{left:113px;top:2233px;width:445px;color:var(--white)}
.join-brand{left:660px;top:2150px;width:370px;text-align:center}
.join-brand .emblem{width:150px;height:150px;margin:0 auto;border-radius:50%;background:rgba(255,255,255,.16)}
.join-brand .name{font-family:var(--head);font-weight:600;font-size:48px;color:var(--white);margin-top:26px}
.join-brand .line{font-size:20px;color:var(--white);margin-top:4px}

/* blog */
.blog h2{position:absolute;left:0;width:1200px;text-align:center;top:2577px}
.blog-img{height:214px}
.img-a{background:linear-gradient(140deg,#e8e6e2,#b9c0c6 50%,#3d4a66)}
.img-b{background:linear-gradient(140deg,#3b3b40,#7d7a78 50%,#d8d3cc)}
.img-c{background:linear-gradient(140deg,#4b4a49,#9ea5ae 50%,#2f3b4e)}
.post{background:var(--white);box-shadow:0 4px 18px rgba(0,0,0,.09);padding:26px 28px 0 28px}
.post .meta{font-size:11.5px;color:var(--red)}
.post h3{font-family:var(--head);font-weight:600;font-size:17px;line-height:28px;color:var(--ink);margin-top:12px}
.post p{font-size:12.5px;line-height:20.5px;color:var(--text);margin-top:12px}
.arrow{width:44px;height:44px;border-radius:50%}
.arrow.l{border:2px solid var(--red);background:var(--white)}
.arrow.r{background:var(--red)}

/* contact */
.contact-band{left:0;top:3209px;width:1200px;height:427px;background:linear-gradient(90deg,#c01f2f,#cd2f3f 50%,#c21f30)}
.contact-title{left:0;width:1200px;text-align:center;top:3264px;color:var(--white)}
.contact-lead{left:250px;width:700px;text-align:center;top:3322px;color:var(--white);font-size:15px;line-height:25px}
.form-card{left:172px;top:3403px;width:857px;height:373px;background:var(--white);box-shadow:0 6px 24px rgba(0,0,0,.1)}
.form-line{left:227px;top:3774px;width:748px;height:4px;background:var(--red)}
.quote-kicker{left:225px;top:3520px;font-size:15px;color:var(--ink)}
.quote-title{left:223px;top:3546px;font-family:var(--head);font-weight:600;font-size:29px;color:var(--ink)}
.quote-text{left:224px;top:3588px;width:260px;font-size:12px;line-height:20px}
.call-label{left:296px;top:3662px;font-size:11px;color:var(--red)}
.call-number{left:296px;top:3680px;font-family:var(--head);font-weight:600;font-size:21px;color:var(--ink)}
.field{position:absolute;background:var(--field);font-size:11px;color:#80858a;padding:12px 10px;border-radius:2px}
.consent{left:722px;top:3690px;display:flex;align-items:center;gap:16px;font-size:12px;color:var(--ink)}
.consent .radio{width:14px;height:14px;border-radius:50%;border:1px solid #ddd;position:relative}
.consent .radio::after{content:"";position:absolute;left:3px;top:3px;width:6px;height:6px;border-radius:50%;background:var(--red)}

/* footer */
.footer{left:0;top:3879px;width:1200px;height:348px;background:var(--footer)}
.f-brand{left:112px;top:3962px}
.f-brand .brand-name{font-size:28px}
.f-follow{left:110px;top:4037px;font-family:var(--head);font-weight:600;font-size:18px;color:var(--white)}
.socials{left:111px;top:4083px;display:flex;gap:7px}
.socials span{width:36px;height:36px;border-radius:50%;background:var(--white);border:2px solid var(--red)}
.socials span:first-child{background:var(--red)}
.f-divider{left:390px;top:3950px;width:1px;height:160px;background:#2a2a2c}
.f-col h4{font-family:var(--head);font-weight:600;font-size:18px;color:var(--white);margin-bottom:14px}
.f-col li{list-style:none;font-size:14px;color:#e6e6e6;line-height:26px;padding-left:25px;position:relative}
.f-col li::before{content:"»";position:absolute;left:0;top:-1px;color:#fff}
.f-contact p{font-size:14px;color:#e6e6e6;line-height:25px;padding-left:23px;position:relative}
.f-contact svg{position:absolute;left:0;top:5px}
.f-rule{left:112px;top:4150px;width:976px;height:1px;background:#2a2a2c}
.copy{left:0;width:1200px;top:4184px;text-align:center;font-size:14px;color:#e6e6e6}
</style>
</head>
<body>

<!-- HERO -->
<section class="abs hero" aria-label="Welcome"></section>
<div class="abs hero-photo" role="img" aria-label="City skyline at dusk with a glowing sunset"></div>
<div class="abs brand">
  <div class="brand-name"><span class="sq"></span>Kestrel Talent</div>
  <div class="brand-line">California Staffing</div>
</div>
<nav class="nav">
  <a style="left:499px">Home</a>
  <a style="left:582px">About Us</a>
  <a style="left:688px">Services</a>
  <a style="left:786px">Blog</a>
  <a style="left:858px">Contact Us</a>
</nav>
<a class="btn login">LOG IN <span class="dot"></span></a>
<div class="abs nav-line"></div>
<div class="abs welcome">Welcome to</div>
<h1 class="abs hero-title">Kestrel Talent</h1>
<div class="abs hero-sub">The Future Of Work</div>
<a class="btn" style="left:112px;top:392px">GET STARTED <span class="dot"></span></a>
<div class="abs slides"><span></span><span></span><span></span></div>

<!-- ABOUT -->
<section class="about">
  <div class="abs about-frame"></div>
  <div class="abs about-photo" role="img" aria-label="Two colleagues reviewing work together at a computer"></div>
  <div class="abs about-block"></div>
  <div class="abs dots" style="left:605px;top:1092px;grid-template-columns:repeat(2,4px);column-gap:20px;row-gap:20px">
    <i></i><i></i><i></i><i></i><i></i><i></i><i></i><i></i>
  </div>
  <div class="abs dots" style="left:476px;top:1195px;grid-template-columns:repeat(8,4px);column-gap:16px;row-gap:20px">
    <i></i><i></i><i></i><i></i><i></i><i></i><i></i><i></i>
    <i></i><i></i><i></i><i></i><i></i><i></i><i></i><i></i>
  </div>
  <h2 class="h2">ABOUT <em>US</em></h2>
  <p class="para">Sed ut perspiciatis unde omnis iste natus error sit voluptatem accusantium doloremque laudantium, totam rem aperiam, eaque ipsa quae ab illo inventore veritatis et quasi architecto beatae vitae dicta sunt explicabo. Nemo enim ipsam voluptatem quia voluptas sit aspernatur aut odit aut fugit, sed quia consequuntur magni dolores eos qui ratione voluptatem sequi nesciunt. Neque porro quisquam est, qui dolorem ipsum quia dolor sit amet, consectetur, adipisci velit, sed quia non numquam eius modi tempora incidunt ut labore et dolore magnam aliquam quaerat voluptatem.</p>
  <a class="btn">LEARN MORE <span class="dot"></span></a>
</section>

<!-- SERVICES -->
<section class="services">
  <h2 class="h2">SERVICES WE<br><em>OFFER</em></h2>
  <p class="para">Sed ut perspiciatis unde omnis iste natus error sit voluptatem accusantium doloremque laudantium, totam rem aperiam, eaque ipsa quae ab illo inventore veritatis et quasi architecto beatae vitae dicta sunt explicabo.</p>
  <div class="abs services-band" role="img" aria-label="Soft blurred office background"></div>
  <div class="abs dots" style="left:928px;top:1440px;grid-template-columns:repeat(6,4px);column-gap:13px;row-gap:13px">
    <i></i><i></i><i></i><i></i><i></i><i></i>
    <i></i><i></i><i></i><i></i><i></i><i></i>
    <i></i><i></i><i></i><i></i><i></i><i></i>
    <i></i><i></i><i></i><i></i><i></i><i></i>
  </div>
  <div class="abs grid">
    <div class="ph-ware" role="img" aria-label="Warehouse aisle with workers and stacked boxes"></div>
    <div class="cell">
      <svg width="46" height="44" viewBox="0 0 46 44" fill="none" stroke="#222" stroke-width="1.6"><path d="M3 16 L23 4 L43 16 V42 H3 Z"/><rect x="12" y="20" width="22" height="22"/><path d="M12 26h22M12 32h22"/><rect x="18" y="34" width="10" height="8" stroke="#c51f30"/></svg>
      <h3>Warehouse and Distribution</h3>
      <p>Lorem ipsum dolor sit amet, consectetur adipiscing elit, sed do eiusmmagna aliqua.</p>
      <a>READ MORE</a>
    </div>
    <div class="ph-acct" role="img" aria-label="Hands working with a calculator and paperwork"></div>
    <div class="cell">
      <svg width="46" height="44" viewBox="0 0 46 44" fill="none" stroke="#222" stroke-width="1.6"><rect x="14" y="2" width="22" height="14"/><path d="M18 7h14M18 11h10" stroke="#c51f30"/><rect x="4" y="16" width="30" height="26"/><path d="M9 23h6M19 23h6M9 30h6M19 30h6M9 37h6M19 37h6"/></svg>
      <h3>Accounting and Finance</h3>
      <p>Lorem ipsum dolor sit amet, consectetur adipiscing elit, sed do eiusmmagna aliqua.</p>
      <a>READ MORE</a>
    </div>
    <div class="cell">
      <svg width="48" height="48" viewBox="0 0 48 48" fill="none" stroke="#222" stroke-width="1.6"><rect x="2" y="4" width="12" height="12"/><rect x="18" y="4" width="12" height="12"/><rect x="34" y="4" width="12" height="12" stroke="#c51f30"/><path d="M8 16v8h32v-8M24 16v10"/><path d="M10 26h16l3 4h11v16H10z"/></svg>
      <h3>Administrative and Office</h3>
      <p>Lorem ipsum dolor sit amet, consectetur adipiscing elit, sed do eiusmmagna aliqua.</p>
      <a>READ MORE</a>
    </div>
    <div class="ph-office" role="img" aria-label="Professionals reviewing documents in a dim office"></div>
    <div class="cell">
      <svg width="56" height="48" viewBox="0 0 56 48" fill="none" stroke="#222" stroke-width="1.6"><circle cx="20" cy="16" r="10" stroke="#c51f30"/><circle cx="20" cy="16" r="4"/><circle cx="38" cy="30" r="6"/><path d="M2 40h52v6H2z"/><circle cx="8" cy="43" r="1.2"/><circle cx="18" cy="43" r="1.2"/><circle cx="28" cy="43" r="1.2"/><circle cx="38" cy="43" r="1.2"/><circle cx="48" cy="43" r="1.2"/></svg>
      <h3>Manufacturing and Production</h3>
      <p>Lorem ipsum dolor sit amet, consectetur adipiscing elit, sed do eiusmmagna aliqua.</p>
      <a>READ MORE</a>
    </div>
    <div class="ph-mfg" role="img" aria-label="Technician assembling industrial machinery"></div>
  </div>
</section>

<!-- JOIN -->
<section class="abs join" role="img" aria-label="Red tinted team meeting backdrop"></section>
<h2 class="abs join-title">INTERESTED IN WORKING<br>FOR KESTREL TALENT?</h2>
<p class="abs para join-text">Sed ut perspiciatis unde omnis iste natus error sit voluptatem accusantium doloremque laudantium, totam rem aperiam, eaque ipsa quae ab illo inventore veritatis et quasi architecto beatae vitae dicta sunt explicabo.</p>
<a class="btn outline" style="left:113px;top:2361px">FIND A JOB <span class="dot"></span></a>
<div class="abs join-brand">
  <div class="emblem"></div>
  <div class="name">Kestrel Talent</div>
  <div class="line">California Staffing</div>
</div>

<!-- BLOG -->
<section class="blog">
  <h2 class="h2">LATEST <em>BLOG</em></h2>
  <div class="abs arrow l" style="left:50px;top:2752px"><svg width="40" height="40" viewBox="0 0 40 40"><path d="M23 12 L15 20 L23 28" fill="none" stroke="#c51f30" stroke-width="2"/></svg></div>
  <div class="abs arrow r" style="left:1100px;top:2752px"><svg width="44" height="44" viewBox="0 0 44 44"><path d="M19 14 L27 22 L19 30" fill="none" stroke="#fff" stroke-width="2.4"/></svg></div>

  <div class="abs blog-img img-a" style="left:112px;top:2667px;width:307px" role="img" aria-label="Professional holding a tablet in a bright office"></div>
  <article class="abs post" style="left:130px;top:2865px;width:270px;height:236px">
    <div class="meta">March 01,2024 | 0 Comments</div>
    <h3>Sed ut perspiciatis unde omnis iste natus</h3>
    <p>Sed ut perspiciatis unde omnis iste natus error sit voluptatem accusantium doloremque laudantium, totam rem aperiam</p>
  </article>

  <article class="abs post" style="left:465px;top:2667px;width:270px;height:214px">
    <div class="meta">March 01,2024 | 0 Comments</div>
    <h3>Sed ut perspiciatis unde omnis iste natus</h3>
    <p>Sed ut perspiciatis unde omnis iste natus error sit voluptatem accusantium doloremque laudantium, totam rem aperiam</p>
  </article>
  <div class="abs blog-img img-b" style="left:447px;top:2906px;width:306px;height:196px" role="img" aria-label="Business team meeting around a table"></div>

  <div class="abs blog-img img-c" style="left:781px;top:2667px;width:306px" role="img" aria-label="Young colleagues collaborating on a laptop"></div>
  <article class="abs post" style="left:798px;top:2865px;width:272px;height:236px">
    <div class="meta">March 01,2024 | 0 Comments</div>
    <h3>Sed ut perspiciatis unde omnis iste natus</h3>
    <p>Sed ut perspiciatis unde omnis iste natus error sit voluptatem accusantium doloremque laudantium, totam rem aperiam</p>
  </article>
</section>

<!-- CONTACT -->
<section class="contact">
  <div class="abs contact-band" role="img" aria-label="Red tinted handshake backdrop"></div>
  <h2 class="abs h2 contact-title">CONTACT US</h2>
  <p class="abs contact-lead">Lorem ipsum dolor sit amet, consectetur adipiscing elit, sed do eiusmod tempor incididunt ut labore et dolore magna aliqua</p>
  <div class="abs form-card"></div>
  <div class="abs form-line"></div>
  <div class="abs dots" style="left:950px;top:3706px;grid-template-columns:repeat(7,4px);column-gap:12px;row-gap:14px">
    <i style="visibility:hidden"></i><i style="visibility:hidden"></i><i style="visibility:hidden"></i><i style="visibility:hidden"></i><i></i><i></i><i></i>
    <i style="visibility:hidden"></i><i style="visibility:hidden"></i><i style="visibility:hidden"></i><i style="visibility:hidden"></i><i></i><i></i><i></i>
    <i style="visibility:hidden"></i><i style="visibility:hidden"></i><i style="visibility:hidden"></i><i style="visibility:hidden"></i><i></i><i></i><i></i>
    <i></i><i></i><i></i><i></i><i></i><i></i><i></i>
    <i></i><i></i><i></i><i></i><i></i><i></i><i></i>
  </div>
  <svg class="abs" style="left:224px;top:3446px" width="50" height="52" viewBox="0 0 50 52" fill="none" stroke="#c51f30" stroke-width="1.6"><path d="M3 20 L25 3 L47 20 V49 H3 Z"/><path d="M3 20 L25 36 L47 20"/><circle cx="25" cy="19" r="5"/><path d="M30 19v2a3 3 0 0 0 6 0v-2a11 11 0 1 0-5 9"/></svg>
  <div class="abs quote-kicker">Get in Touch</div>
  <div class="abs quote-title">Request a Quote</div>
  <p class="abs quote-text">Lorem ipsum dolor sit amet, consectetur adipiscing elit, sed do eiusmod tempor incididunt ut aliqua</p>
  <svg class="abs" style="left:224px;top:3666px" width="60" height="50" viewBox="0 0 60 50"><circle cx="25" cy="25" r="22" fill="#f6e3e5"/><path d="M12 14c3-3 6-2 8 1l3 5c1 2 0 4-2 5l-2 1c2 5 6 9 11 11l1-2c1-2 3-3 5-2l5 3c3 2 4 5 1 8-3 3-8 4-14 1C19 41 11 33 8 26c-3-6-2-9 4-12z" fill="none" stroke="#c51f30" stroke-width="1.6"/></svg>
  <div class="abs call-label">CALL US TODAY!</div>
  <div class="abs call-number">+1 (555) 204 7719</div>

  <div class="field" style="left:522px;top:3452px;width:210px;height:38px">First Name</div>
  <div class="field" style="left:762px;top:3452px;width:208px;height:38px">Last Name</div>
  <div class="field" style="left:522px;top:3514px;width:210px;height:38px">Email</div>
  <div class="field" style="left:762px;top:3514px;width:208px;height:38px">Phone</div>
  <div class="field" style="left:522px;top:3577px;width:448px;height:76px">Additional Details</div>
  <a class="btn" style="left:520px;top:3676px">SUBMIT REQUEST <span class="dot"></span></a>
  <div class="abs consent"><span class="radio"></span>accept the privacy and terms</div>
</section>

<!-- FOOTER -->
<footer>
  <div class="abs footer"></div>
  <div class="abs f-brand">
    <div class="brand-name"><span class="sq"></span>Kestrel Talent</div>
    <div class="brand-line">California Staffing</div>
  </div>
  <div class="abs f-follow">Follow us</div>
  <div class="abs socials" aria-label="Social links"><span></span><span></span><span></span><span></span></div>
  <div class="abs f-divider"></div>
  <div class="abs f-col" style="left:432px;top:3942px">
    <h4>Quick Links</h4>
    <ul><li>Home</li><li>About Us</li><li>Services</li><li>Blog</li><li>Contact Us</li></ul>
  </div>
  <div class="abs f-col" style="left:639px;top:3942px">
    <h4>Our Company</h4>
    <ul><li>Terms &amp; Conditions</li><li>Privacy Policy</li><li>About Us</li><li>Support</li></ul>
  </div>
  <div class="abs f-col f-contact" style="left:864px;top:3942px;width:240px">
    <h4>Contact us</h4>
    <p><svg width="12" height="16" viewBox="0 0 12 16"><path d="M6 0a6 6 0 0 0-6 6c0 4.5 6 10 6 10s6-5.5 6-10a6 6 0 0 0-6-6zm0 8.5A2.5 2.5 0 1 1 6 3.5a2.5 2.5 0 0 1 0 5z" fill="#fff"/></svg>Lorem ipsum dolor sit amet, consectetur adipiscing</p>
    <p style="margin-top:16px"><svg width="14" height="14" viewBox="0 0 14 14"><path d="M3 1c1-1 2 0 3 1l1 2c0 1 0 1-1 2 1 2 2 3 4 4 1-1 1-1 2-1l2 1c1 1 1 2 0 3-2 2-5 1-8-2S1 3 3 1z" fill="#fff"/></svg>1+ (555) 204 7719</p>
    <p style="margin-top:16px"><svg width="15" height="12" viewBox="0 0 15 12"><rect x="0" y="0" width="15" height="12" rx="1" fill="#fff"/><path d="M0 1l7.5 6L15 1" fill="none" stroke="#0c0c0d" stroke-width="1.3"/></svg>info@kestreltalent.com</p>
  </div>
  <div class="abs f-rule"></div>
  <div class="abs copy">©Copyrights 2024 Kestrel Talent &nbsp; | &nbsp; All Rights Reserved</div>
</footer>

</body>
</html>
```